Website for Vornelix Capital, my new firm that raises money from investors to buy, build, own an...

Vornelix Capital needs a website! We are a new company with very experienced people, who invest in, own and build hotel properties, as well as apartments and other commercial real estate. We seek investors for our projects, and we provide safe, secure returns on their investment in our projects. Our new logo is designed to exhibit strength, class and security, and would like our website to continue on this theme. Our name, Vornelix, is a word-play on a Greek word “aristeia”, which means “excellence” and “a warriors finest moment of glory in war”. If you are in business, you realize that much of it is like war, with strategy and moves and opponents and competitors, and ever-changing economic conditions and threats that make business very much like war. We like to think that we are good at business (war), and so have named our company “Vornelix”, using the founders last name and the word “aristeia” combined. Another definition of "aristeia" is "performing at the peak of one's potential after a long struggle"...again, much like business in real life! The website design should exhibit financial security, smart moves, and positive growth towards a bright future.

Target Market(s)

The target market is smart and wealthy investors, with others such as brokers, cities and government agencies, lenders, sellers, partners, etc also looking at it.

Industry/Entity Type

Investment

Number of Pages Required

5+ page

Font styles to use
Sans Serif

Colors
fec214

Requirements
Must have
• Our website should have a landing page, a "about" or bio page, a projects page and a contact us page. Our new logo uses the colors black and gold, so this should be factored in to our site. The site should be simple, yet impactful and impressive. I have actually two logos, which can be mixed and interchanged in a complimentary way, each with their own unique look.
Nice to have
• I have uploaded a couple screenshots of a website i like, and the simplicity I mention.
Should not have
• The site should not be flashy or complicated or complex or "busy"

```html
<!DOCTYPE html>
<html lang="en">
<head>
<meta charset="utf-8">
<title>Vornelix Capital</title>
<link href="https://fonts.googleapis.com/css2?family=Lato:wght@300;400;700;900&family=Raleway:wght@300;400;500&display=swap" rel="stylesheet">
<style>
:root{
  --gold:#fec214;
  --gold-deep:#f2b51a;
  --ink:#1d1d1d;
  --text:#3a3a3a;
  --muted:#b9b9b9;
  --line:#e3e3e3;
  --band:#f1f1f1;
  --white:#ffffff;
}
*{margin:0;padding:0;box-sizing:border-box}
html,body{width:1200px;height:3383px;overflow:hidden;background:var(--white)}
body{position:relative;font-family:'Lato',sans-serif;color:var(--text)}
.abs{position:absolute}
.display{font-family:'Raleway',sans-serif;font-weight:400;color:var(--ink);line-height:1;text-transform:uppercase}

/* hero */
.hero{left:0;top:0;width:1200px;height:720px}
.hero-photo{left:0;top:0;width:1200px;height:720px;background:linear-gradient(180deg,#f7c431 0%,#f0b923 55%,#eab42a 100%)}
.hero-curve{left:0;top:0}
.brand{left:79px;top:70px;display:flex;align-items:center;gap:12px}
.brand-mark{width:18px;height:18px;background:var(--ink)}
.brand-name{font-family:'Lato',sans-serif;font-weight:900;font-size:26px;letter-spacing:2px;color:var(--ink)}
.nav{top:56px;left:0;width:1200px}
.nav a{position:absolute;font-size:13px;color:var(--ink);text-decoration:none;letter-spacing:.5px;text-transform:uppercase}
.hero-title{left:79px;top:312px;font-size:44px;font-weight:900;color:var(--white);letter-spacing:-.5px}
.hero-sub{left:79px;top:374px;width:540px;font-size:19px;line-height:1.25;color:#5a4a10}
.btn-more{left:79px;top:440px;width:205px;height:50px;background:var(--white);color:#2a4a8a;font-size:19px;display:flex;align-items:center;justify-content:center;text-transform:uppercase}
.hero-art{left:587px;top:250px;width:540px;height:460px;border-radius:40px;background:radial-gradient(ellipse at 50% 55%,#8fb6c6 0%,#6d8fa0 45%,rgba(60,70,80,.0) 75%)}

/* about */
.watermark{left:0;top:740px;width:1200px;text-align:center;font-family:'Raleway',sans-serif;font-size:170px;font-weight:500;color:#f6f6f6;letter-spacing:8px}
.about-title{left:79px;top:800px;font-size:42px}
.about-text{left:380px;top:812px;width:660px;font-size:13px;line-height:1.7;color:#9a9a9a}

/* invest */
.invest-title{right:79px;top:975px;font-size:42px;text-align:right}
.card{width:333px;height:298px;top:1083px;background:var(--white);box-shadow:0 4px 22px rgba(0,0,0,.07);text-align:center}
.card svg{margin-top:45px}
.card h3{margin-top:22px;font-family:'Lato',sans-serif;font-weight:400;font-size:23px;color:var(--gold)}
.card p{margin:22px auto 0;width:270px;font-size:13px;line-height:1.6;color:#c3c3c3}

/* testimonial */
.quote-band{left:0;top:1471px;width:1200px;height:311px;background:linear-gradient(180deg,#f5bd27,#f0b72c)}
.quote-text{left:170px;top:1538px;width:860px;text-align:center;font-size:15px;line-height:1.55;color:#5c4c12}
.quote-mark{font-family:Georgia,serif;font-size:60px;color:#f9d978}
.client{left:0;top:1628px;width:1200px;text-align:center;font-size:20px;color:var(--ink)}
.client small{font-size:14px;color:#6a5a20}
.dots{left:575px;top:1680px;display:flex;gap:10px}
.dots i{width:6px;height:6px;border-radius:50%;background:#7a6420;opacity:.5}
.dots i:first-child{opacity:1;background:var(--ink)}
.avatar-ring{left:547px;top:1720px;width:106px;height:106px;border-radius:50%;background:var(--white);box-shadow:0 3px 12px rgba(0,0,0,.2)}
.avatar{left:557px;top:1730px;width:86px;height:86px;border-radius:50%;background:linear-gradient(180deg,#6b4a38,#d9b59c)}

/* projects */
.projects-title{left:0;top:1888px;width:1200px;text-align:center;font-size:42px}
.proj{top:1954px;width:311px;height:388px;background:var(--white);border:1px solid var(--line)}
.proj.active{box-shadow:0 5px 20px rgba(0,0,0,.18);border-color:#d6d6d6}
.proj-img{height:167px}
.proj h4{margin:24px 30px 0;font-family:'Lato',sans-serif;font-weight:400;font-size:18px;line-height:1.3;color:var(--ink);padding-bottom:16px;border-bottom:1px solid var(--line);height:86px;padding-right:20px}
.proj p{margin:14px 30px 0;font-size:13px;line-height:1.55;color:#c0c0c0;height:60px;overflow:hidden}
.proj a{display:block;margin:6px 30px 0;font-size:14px;color:var(--ink);text-decoration:none;text-transform:uppercase}
.proj.active a{text-decoration:underline}
.arrow{top:2128px}

/* newsletter */
.news-band{left:0;top:2407px;width:1200px;height:165px;background:var(--band)}
.news-title{left:79px;top:2445px;font-size:42px;line-height:1.05}
.mail-ring{left:406px;top:2427px;width:125px;height:125px;border-radius:50%;border:1px solid #bfbfbf;background:var(--band)}
.email-field{left:515px;top:2465px;width:390px;height:50px;background:var(--white);font-size:13px;font-style:italic;color:#888;padding:17px 0 0 8px}
.btn-sub{left:915px;top:2465px;width:206px;height:50px;background:var(--ink);color:var(--white);font-size:18px;display:flex;align-items:center;justify-content:center;text-transform:uppercase}

/* latest news */
.latest-title{right:79px;top:2635px;font-size:42px;text-align:right}
.post-img{top:2741px;width:187px;height:120px;background:linear-gradient(180deg,#8fb0cf,#4a5a6e)}
.post-meta{font-size:11px;color:#8a8a8a}
.post-title{margin-top:8px;font-size:21px;color:var(--ink);padding-bottom:10px;border-bottom:1px solid var(--line)}
.post-text{margin-top:10px;font-size:13px;line-height:1.5;color:#8a8a8a}

/* footer */
.footer{left:0;top:2955px;width:1200px;height:428px;background:var(--gold-deep)}
.footer-curve{left:0;top:2900px}
.agent-art{left:0;top:2920px;width:300px;height:310px;border-radius:30px;background:linear-gradient(160deg,#f3a46a 0%,#e8834a 45%,#9b6a5a 100%)}
.foot-h{font-size:17px;color:var(--ink)}
.contact-row{display:flex;gap:22px;align-items:flex-start;font-size:14px;color:var(--white)}
.field{border:1px solid #5a4712;font-size:12px;color:#fff7d8;padding:14px 0 0 14px}
.btn-submit{background:var(--ink);color:var(--white);font-size:19px;display:flex;align-items:center;justify-content:center;text-transform:uppercase}
.foot-line{left:79px;top:3323px;width:1042px;height:1px;background:#c0910e}
.copyright{left:0;top:3343px;width:1200px;text-align:center;font-size:13px;color:var(--ink)}
.copyright span{color:#fff3c8}
</style>
</head>
<body>

<!-- HERO -->
<section class="abs hero">
  <div class="abs hero-photo" role="img" aria-label="Gold-toned photograph of a harbour skyline with cranes"></div>
  <svg class="abs hero-curve" width="1200" height="720" viewBox="0 0 1200 720">
    <path d="M0 618 L640 618 C900 612 1110 470 1200 230 L1200 720 L0 720 Z" fill="#ffffff"/>
    <path d="M0 608 L640 608 C900 602 1110 460 1200 200" fill="none" stroke="#1d1d1d" stroke-width="9"/>
    <path d="M660 630 C930 626 1130 500 1200 300" fill="none" stroke="#d8d8d8" stroke-width="14"/>
  </svg>
  <div class="abs brand"><span class="brand-mark"></span><span class="brand-name">VORNELIX CAPITAL</span></div>
  <nav class="abs nav">
    <a style="left:637px">Home</a>
    <a style="left:751px">About Us</a>
    <a style="left:896px">Project</a>
    <a style="left:1029px">Contact Us</a>
  </nav>
  <h1 class="abs hero-title">LOREM IPSUM DUMMY.</h1>
  <p class="abs hero-sub">Lorem Ipsum is simply dummy text of the printing and typesetting industry.</p>
  <div class="abs btn-more">Learn More</div>
  <div class="abs hero-art" role="img" aria-label="Illustration of three business people meeting around a table on blue sofas"></div>
</section>

<!-- ABOUT -->
<div class="abs watermark" aria-hidden="true">VORNELIX</div>
<h2 class="abs display about-title">Short<br>About Us</h2>
<p class="abs about-text">Lorem Ipsum is simply dummy text of the printing and typesetting industry. Lorem Ipsum has been the industry's standard dummy text ever since the 1500s, when an unknown printer took a galley of type and scrambled it to make a type specimen book.</p>

<!-- WHO INVEST IN -->
<h2 class="abs display invest-title">Who<br>Invest In</h2>
<div class="abs card" style="left:79px">
  <svg width="70" height="80" viewBox="0 0 70 80"><rect x="10" y="14" width="50" height="62" fill="#6a6a6a"/><rect x="26" y="4" width="18" height="10" fill="#6a6a6a"/><g fill="#fff"><rect x="16" y="22" width="8" height="8"/><rect x="31" y="22" width="8" height="8"/><rect x="46" y="22" width="8" height="8"/><rect x="16" y="38" width="8" height="8"/><rect x="31" y="38" width="8" height="8"/><rect x="46" y="38" width="8" height="8"/><rect x="29" y="58" width="12" height="18"/></g></svg>
  <h3>Hotel Property</h3>
  <p>Lorem Ipsum is simply dummy text of the printing and typesetting industry. Lorem Ipsum has been the industry's standard.</p>
</div>
<div class="abs card" style="left:433px">
  <svg width="90" height="80" viewBox="0 0 90 80"><rect x="8" y="8" width="74" height="70" fill="#6a6a6a"/><g fill="#fff"><rect x="16" y="16" width="10" height="10"/><rect x="40" y="16" width="10" height="10"/><rect x="64" y="16" width="10" height="10"/><rect x="16" y="36" width="10" height="10"/><rect x="40" y="36" width="10" height="10"/><rect x="64" y="36" width="10" height="10"/><rect x="38" y="56" width="14" height="22"/></g></svg>
  <h3>Apartments</h3>
  <p>Lorem Ipsum is simply dummy text of the printing and typesetting industry. Lorem Ipsum has been the industry's standard.</p>
</div>
<div class="abs card" style="left:790px">
  <svg width="100" height="80" viewBox="0 0 100 80"><rect x="30" y="2" width="36" height="76" fill="#555"/><rect x="6" y="30" width="30" height="48" fill="#7a7a7a"/><rect x="62" y="22" width="32" height="56" fill="#777"/><g fill="#ddd"><rect x="36" y="10" width="24" height="3"/><rect x="36" y="20" width="24" height="3"/><rect x="36" y="30" width="24" height="3"/><rect x="36" y="40" width="24" height="3"/><rect x="36" y="50" width="24" height="3"/><rect x="12" y="40" width="18" height="3"/><rect x="12" y="52" width="18" height="3"/><rect x="68" y="32" width="20" height="3"/><rect x="68" y="44" width="20" height="3"/></g></svg>
  <h3>Commercial Real Estate</h3>
  <p>Lorem Ipsum is simply dummy text of the printing and typesetting industry. Lorem Ipsum has been the industry's standard.</p>
</div>

<!-- TESTIMONIAL -->
<div class="abs quote-band" role="img" aria-label="Gold-toned photograph of city towers"></div>
<span class="abs quote-mark" style="left:125px;top:1500px">“</span>
<span class="abs quote-mark" style="left:1045px;top:1560px">”</span>
<p class="abs quote-text">Lorem Ipsum is simply dummy text of the printing and typesetting industry. Lorem Ipsum has been the industry's standard dummy text ever since the 1500s, when an unknown printer took a galley of type and scrambled it to make a type specimen book.Lorem Ipsum is simply dummy text of the printing.</p>
<p class="abs client">- Client's Name , <small>Designation</small></p>
<div class="abs dots"><i></i><i></i><i></i></div>
<div class="abs avatar-ring"></div>
<div class="abs avatar" role="img" aria-label="Portrait photograph of the client"></div>

<!-- PROJECTS -->
<h2 class="abs display projects-title">Our Projects</h2>
<svg class="abs arrow" style="left:30px" width="24" height="30" viewBox="0 0 24 30"><path d="M12 6 L4 15 L12 24 M20 6 L12 15 L20 24" fill="none" stroke="#333" stroke-width="2"/></svg>
<svg class="abs arrow" style="left:1146px" width="24" height="30" viewBox="0 0 24 30"><path d="M8 6 L16 15 L8 24" fill="none" stroke="#fec214" stroke-width="3"/></svg>
<article class="abs proj" style="left:122px">
  <div class="proj-img" role="img" aria-label="Photograph of a townhouse complex with parking" style="background:linear-gradient(180deg,#c8d4de 0%,#8a7a6a 55%,#6b7060 100%)"></div>
  <h4>Lorem ipsum dolor sit amet</h4>
  <p>Lorem Ipsum is simply dummy text of the printing and typesetting industry. Lorem Ipsum has been the industry.</p>
  <a>Read More</a>
</article>
<article class="abs proj active" style="left:447px">
  <div class="proj-img" role="img" aria-label="Rendering of a modern white apartment building" style="background:linear-gradient(180deg,#6fa8d8 0%,#dfe6ea 55%,#7f9a6a 100%)"></div>
  <h4>Project Name - Lorem ipsum dolor sit</h4>
  <p>Lorem Ipsum is simply dummy text of the printing and typesetting industry. Lorem Ipsum has been the industry.</p>
  <a>Read More</a>
</article>
<article class="abs proj" style="left:772px">
  <div class="proj-img" role="img" aria-label="Photograph of a brick commercial building" style="background:linear-gradient(180deg,#4f86c6 0%,#8a5a40 55%,#6a7a5a 100%)"></div>
  <h4>Lorem ipsum dolor sit amet</h4>
  <p>Lorem Ipsum is simply dummy text of the printing and typesetting industry. Lorem Ipsum has been the industry.</p>
  <a>Read More</a>
</article>

<!-- NEWSLETTER -->
<div class="abs news-band"></div>
<h2 class="abs display news-title">Subscribe<br>Newsletter</h2>
<div class="abs mail-ring"></div>
<svg class="abs" style="left:446px;top:2475px" width="46" height="30" viewBox="0 0 46 30"><rect x="1.5" y="1.5" width="43" height="27" fill="none" stroke="#fec214" stroke-width="2.5"/><path d="M2 2 L23 17 L44 2" fill="none" stroke="#fec214" stroke-width="2.5"/></svg>
<div class="abs email-field">Enter Your Email Address</div>
<div class="abs btn-sub">Subscribe Now</div>

<!-- LATEST NEWS -->
<h2 class="abs display latest-title">Latest<br>News</h2>
<div class="abs post-img" style="left:79px" role="img" aria-label="Photograph of two smiling business people"></div>
<div class="abs" style="left:288px;top:2745px;width:260px">
  <div class="post-meta">Oct. 20, 2018 / 8PM / Harlow Hall</div>
  <div class="post-title">Loremipsum dummy text.</div>
  <div class="post-text">Lorem Ipsum is simply dummy text of the printing and typesetting industry.</div>
</div>
<div class="abs post-img" style="left:622px;background:linear-gradient(160deg,#e9e9e9,#8a8a8a)" role="img" aria-label="Photograph of financial documents and a pen"></div>
<div class="abs" style="left:832px;top:2745px;width:289px">
  <div class="post-meta">Sept. 15, 2018 / 8PM / Harlow Hall</div>
  <div class="post-title">Loremipsum dummy text.</div>
  <div class="post-text">Lorem Ipsum is simply dummy text of the printing and typesetting industry.</div>
</div>

<!-- FOOTER -->
<footer>
  <div class="abs footer"></div>
  <svg class="abs footer-curve" width="1200" height="120" viewBox="0 0 1200 120">
    <path d="M0 0 L0 20 C200 30 420 50 600 55 C760 58 980 56 1200 55 L1200 0 Z" fill="#ffffff"/>
    <path d="M0 20 C200 30 420 50 600 55" fill="none" stroke="#d8d8d8" stroke-width="10"/>
  </svg>
  <div class="abs agent-art" role="img" aria-label="Illustration of a cartoon support agent with a headset at a laptop desk"></div>

  <div class="abs" style="left:311px;top:3060px">
    <div class="foot-h">Contact Us</div>
    <div class="contact-row" style="margin-top:26px">
      <svg width="16" height="22" viewBox="0 0 16 22"><path d="M8 21 C3 14 1 11 1 8 A7 7 0 0 1 15 8 C15 11 13 14 8 21 Z" fill="#7a5f12"/><circle cx="8" cy="8" r="2.6" fill="#f2b51a"/></svg>
      <span style="width:260px;line-height:1.3">123, Lorem Ipsum is simply dummy text of the printing and typesetting industry.</span>
    </div>
    <div class="contact-row" style="margin-top:24px;align-items:center">
      <svg width="18" height="18" viewBox="0 0 18 18"><path d="M3 1 L7 1 L8 5 L6 7 C7 10 8 11 11 12 L13 10 L17 11 L17 15 C17 16 16 17 15 17 C7 17 1 11 1 3 C1 2 2 1 3 1 Z" fill="#7a5f12"/></svg>
      <span style="font-size:21px">123 456 7878</span>
    </div>
    <div class="contact-row" style="margin-top:30px;align-items:center">
      <svg width="20" height="14" viewBox="0 0 20 14"><rect x="0" y="0" width="20" height="14" fill="#7a5f12"/><path d="M0 0 L10 8 L20 0" fill="none" stroke="#f2b51a" stroke-width="1.5"/></svg>
      <span>info@vornelix.com</span>
    </div>
  </div>

  <div class="abs foot-h" style="left:625px;top:3060px">Keep In Touch</div>
  <div class="abs field" style="left:625px;top:3100px;width:228px;height:45px">Your Name:</div>
  <div class="abs field" style="left:625px;top:3158px;width:228px;height:45px">E-Mail:</div>
  <div class="abs field" style="left:625px;top:3218px;width:228px;height:45px">Subject:</div>
  <div class="abs field" style="left:863px;top:3100px;width:258px;height:103px">Message:</div>
  <div class="abs btn-submit" style="left:863px;top:3218px;width:258px;height:45px">Submit</div>

  <div class="abs foot-line"></div>
  <p class="abs copyright">© VORNELIX CAPITAL - 2018. <span>All Rights Reserved.</span></p>
</footer>

</body>
</html>
```